Spring Detox sale graphics for social media

You MUST read the Brief in the WORD document and follow the instructions there. I want to create 10 social media graphics (new Instagram size 4:5 (1080 x 1350 pixels) focusing on our Mother’s Day Spring Detox Sale graphics, using any of the pics attached. Use the attached pics, NO RANDOM STOCK PHOTOGRAPHY. For the color scheme of the graphics, they should all be complementary to the product colors or feel like Spring time.

Target Market(s)

primarily women

Requirements
Must have
• the photos and text attached

```html
<!DOCTYPE html>
<html lang="en">
<head>
<meta charset="utf-8">
<title>Mother's Day Spring Detox Sale</title>
<link rel="stylesheet" href="https://fonts.googleapis.com/css2?family=Bebas+Neue&family=Playfair+Display:ital,wght@1,400&family=Poppins:wght@400;700;800&display=swap">
<style>
  :root {
    --plum-deep: #4e0d2e;
    --plum: #7a2f56;
    --plum-dark: #652447;
    --mauve: #b3597f;
    --rose: #e586ba;
    --white: #ffffff;
    --arrow: #f3ecef;
    --page: #ffffff;
  }
  html, body {
    margin: 0;
    padding: 0;
    width: 1200px;
    height: 2667px;
    overflow: hidden;
    background: var(--page);
  }
  .canvas { position: relative; width: 1200px; height: 2667px; }
  .post {
    position: absolute;
    width: 1200px;
    height: 1513px;
    overflow: hidden;
    background: linear-gradient(180deg, var(--mauve) 0%, var(--plum) 45%, var(--plum-dark) 100%);
  }
  .post--main { left: 0; top: 0; }
  .post--preview { left: 240px; top: 1637px; transform: scale(0.6); transform-origin: top left; }
  .photo {
    position: absolute;
    left: 520px; top: 0; width: 680px; height: 1513px;
    background:
      linear-gradient(90deg, rgba(122,47,86,1) 0%, rgba(122,47,86,0) 22%),
      radial-gradient(ellipse at 60% 55%, #f4e6ee 0%, #d9a8bf 35%, rgba(190,110,140,0.6) 60%, rgba(160,70,90,0.5) 100%),
      linear-gradient(180deg, #b9606e 0%, #a45470 50%, #8c3c5c 100%);
  }
  .products {
    position: absolute;
    left: 390px; top: 1060px; width: 810px; height: 400px;
    background: linear-gradient(90deg, rgba(122,47,86,0) 0%, rgba(245,236,241,0.85) 25%, rgba(245,236,241,0.85) 100%);
  }
  .title {
    position: absolute; left: 62px; margin: 0;
    font-family: "Bebas Neue", "Oswald", sans-serif;
    font-weight: 400; font-size: 218px; line-height: 1;
    color: var(--plum-deep); letter-spacing: -2px;
  }
  .title--mothers { top: 48px; }
  .title--day { top: 222px; }
  .script {
    position: absolute; margin: 0;
    font-family: "Playfair Display", serif; font-style: italic;
    font-weight: 400; font-size: 150px; line-height: 1; color: var(--white);
  }
  .script--spring { left: 302px; top: 225px; }
  .script--detox { left: 208px; top: 360px; }
  .sale {
    position: absolute; left: 56px; top: 470px; margin: 0;
    font-family: "Poppins", sans-serif; font-weight: 400;
    font-size: 278px; line-height: 1; color: var(--rose); letter-spacing: -4px;
  }
  .offer {
    position: absolute; left: 58px; margin: 0;
    font-family: "Poppins", sans-serif; color: var(--white); line-height: 1;
    text-shadow: 0 6px 24px rgba(60,10,35,0.35);
  }
  .offer--amount { top: 740px; font-weight: 800; font-size: 208px; letter-spacing: -6px; }
  .offer--scope { top: 925px; font-weight: 700; font-size: 138px; letter-spacing: -3px; }
  .arrow { position: absolute; left: 0; top: 1135px; width: 330px; height: 240px; }
</style>
</head>
<body>
<div class="canvas">
  <section class="post post--main">
    <div class="photo" role="img" aria-label="Smiling woman in a white sweater standing in a kitchen"></div>
    <div class="products" role="img" aria-label="Row of supplement bottles and cream pumps on a counter"></div>
    <h1 class="title title--mothers">MOTHER’S</h1>
    <p class="title title--day">DAY</p>
    <p class="script script--spring">Spring</p>
    <p class="script script--detox">Detox</p>
    <p class="sale">Sale</p>
    <p class="offer offer--amount">25% Off</p>
    <p class="offer offer--scope">Everything</p>
    <svg class="arrow" viewBox="0 0 330 240" aria-hidden="true">
      <polygon fill="var(--arrow)" points="0,60 120,60 120,0 328,118 120,237 120,172 0,172"/>
    </svg>
  </section>

  <section class="post post--preview">
    <div class="photo" role="img" aria-label="Smiling woman in a white sweater standing in a kitchen"></div>
    <div class="products" role="img" aria-label="Row of supplement bottles and cream pumps on a counter"></div>
    <p class="title title--mothers">MOTHER’S</p>
    <p class="title title--day">DAY</p>
    <p class="script script--spring">Spring</p>
    <p class="script script--detox">Detox</p>
    <p class="sale">Sale</p>
    <p class="offer offer--amount">25% Off</p>
    <p class="offer offer--scope">Everything</p>
    <svg class="arrow" viewBox="0 0 330 240" aria-hidden="true">
      <polygon fill="var(--arrow)" points="0,60 120,60 120,0 328,118 120,237 120,172 0,172"/>
    </svg>
  </section>
</div>
</body>
</html>
```